Meridale Real Estate

We are looking for help with web design for a new company that is revolutionizing the real estate world on the listing side: by charing per hour for top level professional real estate services. We would like the concept to be simple, clean and easily understood.
Updates

We want this website to actually function, not just a static design.

Industry/Entity Type

Real Estate

```html
<!DOCTYPE html>
<html lang="en">
<head>
<meta charset="utf-8">
<title>Meridale Real Estate</title>
<link href="https://fonts.googleapis.com/css2?family=Questrial&family=Open+Sans:wght@400;600;700&display=swap" rel="stylesheet">
<style>
:root{
  --header-bg:#2e3a46;
  --accent:#3ab0e2;
  --btn-top:#5cc6f0;
  --btn-bottom:#2a9ad6;
  --ink:#2a2a2a;
  --muted:#8a8a8a;
  --body:#666;
  --line:#dcdcdc;
  --footer-bg:#262626;
  --footer-text:#e8e8e8;
  --footer-link:#d0d0d0;
  --white:#fff;
}
*{box-sizing:border-box;margin:0;padding:0}
html,body{width:746px;height:1200px;overflow:hidden;background:var(--white)}
body{position:relative;font-family:"Open Sans",sans-serif;color:var(--body)}
.abs{position:absolute}

/* header */
.site-header{left:0;top:0;width:746px;height:86px;background:linear-gradient(180deg,#3c4a58,var(--header-bg))}
.brand{left:56px;top:30px;display:flex;align-items:center;gap:8px;color:var(--white);font-family:"Questrial",sans-serif;font-size:12px;letter-spacing:2px;line-height:14px}
.brand-dot{width:22px;height:22px;border-radius:50%;border:2px solid var(--white)}
.search{left:460px;top:18px;width:152px;height:16px;border-radius:9px;background:#1e262e;border:1px solid #5a6672;font-size:6.5px;font-style:italic;color:#9aa4ae;padding:3px 9px;line-height:9px}
.search svg{position:absolute;right:7px;top:3px}
.header-social{left:632px;top:16px;display:flex;gap:7px}
.header-social span{width:17px;height:17px;border-radius:50%;background:var(--white)}
.main-nav{left:289px;top:51px;display:flex;font-family:"Questrial",sans-serif;font-size:11.5px;color:var(--white)}
.main-nav a{color:inherit;text-decoration:none;padding:0 11px;border-left:1px solid #6b7783;line-height:14px}
.main-nav a:first-child{border:0;padding-left:0;color:var(--accent)}

/* hero */
.hero{left:0;top:86px;width:746px;height:304px;background:linear-gradient(180deg,#6d9fd8 0%,#b9d4ee 38%,#9a7a5c 52%,#8a6a4e 70%,#5f9a34 82%,#4c8a28 100%)}
.hero-title{left:0;top:194px;width:746px;text-align:center;font-family:"Questrial",sans-serif;font-size:26px;color:var(--white);text-shadow:0 1px 3px rgba(0,0,0,.45)}
.hero-sub{left:0;top:230px;width:746px;text-align:center;font-family:"Questrial",sans-serif;font-size:19px;color:var(--white);text-shadow:0 1px 3px rgba(0,0,0,.45)}
.hero-dots{left:348px;top:370px;display:flex;gap:4px}
.hero-dots span{width:9px;height:9px;border-radius:50%;background:rgba(255,255,255,.45)}
.hero-dots span:first-child{background:var(--white)}

/* welcome */
.welcome-title{left:0;top:418px;width:746px;text-align:center;font-family:"Questrial",sans-serif;font-size:22px;color:var(--ink)}
.welcome-text{left:76px;top:447px;width:594px;text-align:center;font-size:8.6px;line-height:15px;color:var(--body)}

/* cards */
.card{top:518px;width:199px;height:200px;border:1px solid var(--line);background:var(--white);text-align:center}
.card-media{height:91px}
.card-title{margin-top:11px;font-family:"Questrial",sans-serif;font-size:15.5px;color:var(--ink)}
.card-text{margin:4px auto 0;width:160px;font-size:7.6px;line-height:12.6px;color:#9a9a9a}
.btn{display:inline-block;margin-top:8px;width:71px;height:20px;line-height:20px;border-radius:3px;background:linear-gradient(180deg,var(--btn-top),var(--btn-bottom));color:var(--white);font-size:7.8px;text-decoration:none;box-shadow:0 1px 2px rgba(0,0,0,.2)}

/* about */
.about{left:52px;top:768px;width:390px}
.about h2{font-family:"Questrial",sans-serif;font-weight:400;font-size:20px;color:var(--ink);margin-bottom:5px}
.about .lead{font-size:9.8px;line-height:14px;color:#777;margin-bottom:7px}
.about p{font-size:7.8px;line-height:14px;color:#777;margin-bottom:6px}

/* gallery */
.gallery{left:466px;top:760px;width:228px;height:181px;border:1px solid #d6d6d6;background:linear-gradient(180deg,#fff 60%,#f0f0f0)}
.gallery h3{position:absolute;left:16px;top:14px;font-family:"Questrial",sans-serif;font-weight:400;font-size:15.5px;color:var(--accent)}
.thumb{position:absolute;width:58px;height:53px;padding:2px;background:var(--white);box-shadow:0 1px 3px rgba(0,0,0,.25)}
.thumb div{width:100%;height:100%}

/* footer */
.footer-rule{left:0;top:982px;width:746px;height:5px;background:repeating-linear-gradient(45deg,#cfcfcf 0 1px,#efefef 1px 3px)}
.site-footer{left:0;top:987px;width:746px;height:213px;background:var(--footer-bg)}
.footer-col{top:1013px}
.footer-col h4{font-weight:400;font-size:12.5px;color:var(--footer-text);margin-bottom:5px;font-family:"Open Sans",sans-serif}
.footer-col li{list-style:none;font-size:8px;line-height:15.8px;color:var(--footer-link)}
.footer-col .phone{font-size:11px;line-height:17px;color:var(--footer-text)}
.footer-col .addr{font-size:8px;line-height:14px;color:var(--footer-link)}
.footer-divider{left:62px;top:1148px;width:633px;height:1px;background:#3d3d3d}
.copyright{left:63px;top:1165px;font-size:6.5px;font-weight:700;color:var(--footer-link)}
.footer-social{left:602px;top:1163px;display:flex;gap:6px}
.footer-social span{width:15px;height:15px;border-radius:2px}
</style>
</head>
<body>

<header class="abs site-header">
  <div class="abs brand"><span class="brand-dot"></span><span>MERIDALE<br>REAL ESTATE</span></div>
  <div class="abs search">Search here..
    <svg width="9" height="9" viewBox="0 0 10 10"><circle cx="4" cy="4" r="3" fill="none" stroke="#9aa4ae" stroke-width="1.2"/><line x1="6.3" y1="6.3" x2="9" y2="9" stroke="#9aa4ae" stroke-width="1.2"/></svg>
  </div>
  <div class="abs header-social" aria-label="Social links"><span></span><span></span><span></span></div>
  <nav class="abs main-nav">
    <a href="#">HOME</a><a href="#">COMMERCIAL</a><a href="#">RESIDENTIAL</a><a href="#">FARM</a><a href="#">LAND</a><a href="#">CONTACT</a>
  </nav>
</header>

<section class="abs hero" role="img" aria-label="Brick country house on a green lawn under a blue sky"></section>
<h1 class="abs hero-title">BUYER AND SELLER REPRESENTATION</h1>
<p class="abs hero-sub">COMMERCIAL &amp; RESIDENTIAL</p>
<div class="abs hero-dots"><span></span><span></span><span></span><span></span></div>

<h2 class="abs welcome-title">Welcome to Properties by Halden homepage</h2>
<p class="abs welcome-text">Phasellus felis dolor scelerisque a tempus eget lobortis id libero Aliquam nec erat at purus cursus interdum Vestibulum ligula augue bibendum accumsan vestibulum ut commodo a mi Morbi ornare gravida elit Integer congue augue et malesuada iaculis ipsum dui aliquet felis at cursus magna nisl nec elit Vestibulum gravida Praesent elementum elit at tellus Malesuada nec ultricies sit amet porttitor</p>

<article class="abs card" style="left:64px">
  <div class="card-media" role="img" aria-label="Modern luxury kitchen interior" style="background:linear-gradient(180deg,#e9e6e1,#b9b2a8)"></div>
  <h3 class="card-title">Luxury Home</h3>
  <p class="card-text">Mauris neque metus malesuada nec ultri-cies sit amet porttitor mattis enim. In massa libero interdum nec</p>
  <a class="btn" href="#">VIEW MORE</a>
</article>
<article class="abs card" style="left:274px">
  <div class="card-media" role="img" aria-label="Glass office tower against a blue sky" style="background:linear-gradient(160deg,#cfe3f5,#3d7fbf 55%,#1f4f80)"></div>
  <h3 class="card-title">Office Buildings</h3>
  <p class="card-text">Mauris neque metus malesuada nec ultri-cies sit amet porttitor mattis enim. In massa libero interdum nec</p>
  <a class="btn" href="#">VIEW MORE</a>
</article>
<article class="abs card" style="left:485px">
  <div class="card-media" role="img" aria-label="Rolling farmland with rows of trees" style="background:linear-gradient(180deg,#c9d6d8 0%,#8e9a5c 35%,#a48a4a 70%,#7d7a3a)"></div>
  <h3 class="card-title">Farms &amp; Ranches</h3>
  <p class="card-text">Mauris neque metus malesuada nec ultri-cies sit amet porttitor mattis enim. In massa libero interdum nec</p>
  <a class="btn" href="#">VIEW MORE</a>
</article>

<section class="abs about">
  <h2>About Our Company</h2>
  <p class="lead">Pellentesque faucibus Ut accumsan ultricies elit Maecenas at justo id velit placerat mo-lestie Donec dictum lectus non odio Cras a ante vitae enim iaculis aliquam</p>
  <p>Duis tincidunt lectus quis dui viverra vestibulum. Suspendisse vulputate aliquam dui. Nulla elemen-tum dui ut augue. Aliquam vehicula mi at mauris. Maecenas placerat, nisl at consequat rhoncus, sem nunc gravida justo, quis eleifend arcu velit quis lacus.</p>
  <p>Aliquam nec erat at purus cursus interdum Vestibulum ligula augue bibendum accumsan vestibulum ut commodo a mi Morbi ornare gravida elit Integer congue augue et malesuada iaculis ipsum dui aliquet felis at cursus , imperdiet vitae, tellus.</p>
</section>

<aside class="abs gallery">
  <h3>OUR GALLERY</h3>
  <div class="thumb" style="left:16px;top:43px"><div role="img" aria-label="Farmhouse in a golden field" style="background:linear-gradient(180deg,#6fa4dc,#c9a35a)"></div></div>
  <div class="thumb" style="left:86px;top:43px"><div role="img" aria-label="Office building" style="background:linear-gradient(180deg,#a9c6e6,#5d7a96)"></div></div>
  <div class="thumb" style="left:155px;top:43px"><div role="img" aria-label="Bright living room interior" style="background:linear-gradient(180deg,#e8dcc4,#a8864f)"></div></div>
  <div class="thumb" style="left:16px;top:106px"><div role="img" aria-label="Terrace with sea view" style="background:linear-gradient(180deg,#8fc3e6,#3a6f8a)"></div></div>
  <div class="thumb" style="left:86px;top:106px"><div role="img" aria-label="Suburban family house" style="background:linear-gradient(180deg,#b8cde0,#6b6b62)"></div></div>
  <div class="thumb" style="left:155px;top:106px"><div role="img" aria-label="Large brick home with lawn" style="background:linear-gradient(180deg,#6fa0d8,#6a4c3a 60%,#4d7a2c)"></div></div>
</aside>

<div class="abs footer-rule"></div>
<footer class="abs site-footer"></footer>

<div class="abs footer-col" style="left:66px"><h4>About us</h4><ul><li>About Us</li><li>Commercial</li><li>Residential</li><li>Farms</li><li>Land</li></ul></div>
<div class="abs footer-col" style="left:179px"><h4>Featured</h4><ul><li>Buying</li><li>Selling</li><li>Leasing</li><li>Investment</li><li>Service Area</li></ul></div>
<div class="abs footer-col" style="left:297px"><h4>Sublinks</h4><ul><li>Lenders</li><li>Architects</li><li>Builders</li><li>Other Services</li><li>Local Links</li></ul></div>
<div class="abs footer-col" style="left:417px"><h4>Support</h4><ul><li>Support</li><li>Testimonials</li><li>Contact Us</li></ul></div>
<div class="abs footer-col" style="left:534px"><h4>Contact Information</h4>
  <p class="addr">1187 Larkspur Ridge Road<br>Brookvale, CA 95410<br>BRE#00000000</p>
  <p class="phone">555.014.2200<br>555.019.3344</p>
</div>

<div class="abs footer-divider"></div>
<p class="abs copyright">© Copyrights 2015 Meridale Real Estate. All Right Reserved</p>
<div class="abs footer-social" aria-label="Social links">
  <span style="background:#3b5998"></span><span style="background:#39a9e0"></span><span style="background:#1a74b0"></span><span style="background:#e8832a"></span>
</div>

</body>
</html>
```